Thornbury Building Company - Card Design

I am looking to use the logo designs that you already did for me to develop a business card. I would like the card to have a black background and be double sided. I want white and green logo and text. I have attached an inspiration photo of a look that I like. I would like to use the Vertical Logo attached to take up the full front side of the card. On the back where I have my name and information, I would like to have the horizontal logo or maybe even just the image of the 'A' and trees without the text. I am open, but I am looking for something clean and simple and I want the green to really pop! Additional files can be found under Design #: 58302946

Target Market(s)

Homeowners

Industry/Entity Type

Construction

Contact Information for Business Card

Name: Marcus Thornbury, Title: Project Manager, Phone: 555.274.8136, Email: thornburybuildingcompany@mailvesta.com, address: 487 Larkspur Ln, Brookvale, OR 95033, Lic# 2468317

Colors
00AB8E
00BBA5
67D7C9
C6EFE9
E9F9F6

Requirements
Nice to have
• I would like to see the logos that I have already got from ArtLoomHub, though I am open to new ones

```html
<!DOCTYPE html>
<html lang="en">
<head>
<meta charset="utf-8">
<title>Thornbury Building Company – Business Card</title>
<link href="https://fonts.googleapis.com/css2?family=Lato:wght@400;700;900&display=swap" rel="stylesheet">
<style>
  :root {
    --backdrop: #5a3c2a;
    --card: #252325;
    --green: #6cbf4a;
    --white: #ffffff;
    --muted: #e8e8e8;
  }
  * { margin: 0; padding: 0; box-sizing: border-box; }
  html, body {
    width: 1200px; height: 977px; overflow: hidden;
    background: var(--backdrop);
    font-family: "Lato", sans-serif;
  }
  .canvas { position: relative; width: 1200px; height: 977px; }
  .card {
    position: absolute;
    width: 640px; height: 366px;
    background: var(--card);
    border-radius: 22px;
    box-shadow: 0 10px 24px rgba(0,0,0,.35);
    overflow: hidden;
  }
  .card--front { left: 90px; top: 90px; }
  .card--back { left: 470px; top: 520px; }

  /* front: company name lockup */
  .front-lockup {
    position: absolute; inset: 0;
    display: flex; flex-direction: column; align-items: center; justify-content: center;
    gap: 22px;
  }
  .brand-dot {
    width: 70px; height: 70px; border-radius: 50%;
    background: var(--green);
  }
  .brand-name {
    color: var(--white);
    font-weight: 900;
    font-size: 40px;
    letter-spacing: 3px;
    text-transform: uppercase;
    text-align: center;
    line-height: 1.15;
  }

  /* back: mark + contact block */
  .back-brand {
    position: absolute; left: 40px; top: 0; bottom: 0; width: 230px;
    display: flex; flex-direction: column; align-items: center; justify-content: center; gap: 16px;
  }
  .back-brand .brand-dot { width: 56px; height: 56px; }
  .back-brand .brand-name { font-size: 22px; letter-spacing: 2px; }
  .divider {
    position: absolute; left: 300px; top: 96px; width: 2px; height: 196px;
    background: var(--green);
  }
  .contact {
    position: absolute; left: 326px; top: 92px; right: 20px;
    color: var(--white);
  }
  .contact__name {
    font-weight: 900; font-size: 26px; text-transform: uppercase; letter-spacing: .3px;
  }
  .contact__title {
    color: var(--green); font-size: 17px; margin-top: 1px; margin-bottom: 12px;
  }
  .contact__list { list-style: none; font-size: 13.5px; color: var(--muted); }
  .contact__item { display: flex; align-items: flex-start; gap: 8px; line-height: 1.4; margin-bottom: 3px; }
  .contact__item svg { width: 12px; height: 12px; flex: none; margin-top: 3px; fill: var(--green); }
  .contact__license { font-size: 13.5px; color: var(--muted); margin-top: 8px; padding-left: 20px; }
</style>
</head>
<body>
<main class="canvas">
  <section class="card card--front" aria-label="Card front">
    <div class="front-lockup">
      <div class="brand-dot"></div>
      <div class="brand-name">Thornbury<br>Building Company</div>
    </div>
  </section>

  <section class="card card--back" aria-label="Card back">
    <div class="back-brand">
      <div class="brand-dot"></div>
      <div class="brand-name">Thornbury</div>
    </div>
    <div class="divider"></div>
    <div class="contact">
      <div class="contact__name">Marcus Thornbury</div>
      <div class="contact__title">Project Manager</div>
      <ul class="contact__list">
        <li class="contact__item">
          <svg viewBox="0 0 12 12"><path d="M6 0a4 4 0 0 0-4 4c0 3 4 8 4 8s4-5 4-8a4 4 0 0 0-4-4zm0 5.5A1.5 1.5 0 1 1 6 2.5a1.5 1.5 0 0 1 0 3z"/></svg>
          <span>487 Larkspur Ln<br>Brookvale, OR 95033</span>
        </li>
        <li class="contact__item">
          <svg viewBox="0 0 12 12"><path d="M2.5 0.5 4.5 3 3.3 4.4c.7 1.6 2.2 3.1 3.8 3.8L8.5 7l2.5 2-1 2C5.5 11 1 6.5 1 1.5z"/></svg>
          <span>555.274.8136</span>
        </li>
        <li class="contact__item">
          <svg viewBox="0 0 12 12"><path d="M0 2h12v1L6 7 0 3zM0 4.2l6 4 6-4V10H0z"/></svg>
          <span>thornburybuildingcompany@mailvesta.com</span>
        </li>
        <li class="contact__item">
          <svg viewBox="0 0 12 12"><circle cx="6" cy="6" r="5.5"/></svg>
          <span>thornburybuildingcompany.com</span>
        </li>
      </ul>
      <div class="contact__license">Lic# 2468317</div>
    </div>
  </section>
</main>
</body>
</html>
```